Business card design for a dynamic IT consulting company

We need a business card design for a young firm, specialized in the Telecommunications/Consulting industry. The name of the company is Quindor and Partners Business Consulting Ltd. (Short name: Quindor and Partnes)
Quindor = solve read reverse, so we aim to be uncomplicated and solution-oriented. The small pipe in our logo is also related to the word solve. So we need a new business card design, which is simple, eye catching and something non traditional (I would probably prefer a square shaped design rather than a rectangle, but open for suggestions). Attached our logo.

Target Market(s)

Usually our customers are Tier1 Telecoms providers (Q-Netra, Palorix, etc) and their executives.

Industry/Entity Type

Business

Contact Information for Business Card

Name: Bence Tolnavari
Email: b.tolnavari@quindor.hu
Web: www.quindor.hu
Mobile: +36 30 518 2769
Title: Managing Director

Optional:
Company name: Quindor and Partners Ltd.
Address: 1087 Budapest, Tolvenka str. 28/C, Hungary

Font styles to use
Other font styles liked:
• helveticaneue_medium, Prime Regular are used now.

Colors

Designer to choose colors to be used in the design.

Requirements
Must have
• I would like to have a 2 sided design.
Nice to have
• I thought if we make the logo a bit bigger (without the company name), that could go to the back with the company name below. I though, if the pipe in the logo is somehow touchable on the business card, would be nice and unique.

```html
<!DOCTYPE html>
<html lang="en">
<head>
<meta charset="UTF-8">
<title>Quindor and Partners – Business Card</title>
<link href="https://fonts.googleapis.com/css2?family=Source+Sans+3:wght@400;600;700&display=swap" rel="stylesheet">
<style>
  :root {
    --backdrop: #8e5552;
    --card-white: #ffffff;
    --brand-blue: #29abe2;
    --name-blue: #1fa0dd;
    --accent-magenta: #b3278f;
    --ink: #1e1e1e;
    --rule: #e3e3e3;
  }
  * { margin: 0; padding: 0; box-sizing: border-box; }
  html, body {
    width: 1200px;
    height: 900px;
    overflow: hidden;
    background: var(--backdrop);
    font-family: "Source Sans 3", Arial, sans-serif;
  }
  .canvas { position: relative; width: 1200px; height: 900px; }

  .card {
    position: absolute;
    top: 170px;
    width: 347px;
    height: 561px;
  }
  .card--front { left: 259px; background: var(--card-white); text-align: center; color: var(--ink); }
  .card--back { left: 631px; background: var(--brand-blue); }

  .holder-name {
    position: absolute; top: 250px; left: 0; right: 0;
    top: 80px;
    font-size: 23px; font-weight: 700; color: var(--name-blue);
  }
  .holder-title {
    position: absolute; top: 111px; left: 0; right: 0;
    font-size: 15.5px; font-weight: 400;
  }
  .divider {
    position: absolute; left: 80px; width: 194px; height: 1px;
    background: var(--rule);
  }
  .divider--upper { top: 157px; }
  .divider--lower { top: 277px; left: 82px; }

  .contact-list {
    position: absolute; top: 183px; left: 0; right: 0;
    list-style: none; font-size: 15.5px; line-height: 20px;
  }
  .contact-label { color: var(--accent-magenta); font-weight: 700; }

  .company-address {
    position: absolute; top: 297px; left: 0; right: 0;
    font-style: normal; font-size: 15.5px; line-height: 20px;
  }

  .front-brand {
    position: absolute; top: 452px; left: 0; right: 0;
    display: flex; justify-content: center; align-items: center; gap: 8px;
    font-size: 15px; font-weight: 600; color: var(--name-blue);
  }
  .front-brand-square { width: 11px; height: 11px; background: var(--accent-magenta); }

  .back-brand {
    position: absolute;
    left: 173px; top: 300px;
    transform: translate(-50%, -50%) rotate(-90deg);
    display: flex; align-items: center; gap: 14px;
    white-space: nowrap;
    font-size: 40px; font-weight: 400; color: var(--card-white);
    letter-spacing: 0.5px;
  }
  .back-brand-square { width: 16px; height: 16px; background: var(--card-white); }
</style>
</head>
<body>
<main class="canvas">
  <section class="card card--front" aria-label="Card front">
    <h1 class="holder-name">Bence Tolnavari</h1>
    <p class="holder-title">Managing Director</p>
    <div class="divider divider--upper"></div>
    <ul class="contact-list">
      <li><span class="contact-label">M</span>: +36 30 518 2769</li>
      <li><span class="contact-label">E</span>: b.tolnavari@quindor.hu</li>
      <li><span class="contact-label">W</span>: www.quindor.hu</li>
    </ul>
    <div class="divider divider--lower"></div>
    <address class="company-address">
      Quindor and Partners Ltd.<br>
      1087 Budapest, Tolvenka str.<br>
      28/C, Hungary
    </address>
    <div class="front-brand">
      <span class="front-brand-square"></span>
      <span>Quindor and Partners</span>
    </div>
  </section>

  <section class="card card--back" aria-label="Card back">
    <div class="back-brand">
      <span class="back-brand-square"></span>
      <span>Quindor &amp; Partners</span>
    </div>
  </section>
</main>
</body>
</html>
```